Insurance Agency website design for Brellow Cover Insurance, LP

Build a website for Brellow Cover Insurance, LP which sells Homeowners, Auto, Renters, Condo, Flood, Disability, Life, Umbrella, and health insurance. We need the coolest insurance agency website out there to get quotes, contact us, or get additional information. Please list the following insurance companies we work with: Varnix, Ostle, Meridale Mutual, Quillor, Dunmarrow, KGZ, and Pellwick.

Make a design similar to https://www.fernagentry.com/

Selling personal insurance policies

```html
<!DOCTYPE html>
<html lang="en">
<head>
<meta charset="utf-8">
<title>Brellow Cover Insurance, LP</title>
<link href="https://fonts.googleapis.com/css2?family=Poppins:wght@400;500;600;700&display=swap" rel="stylesheet">
<style>
:root{
  --navy:#1a2f86;
  --navy-dark:#12236b;
  --green:#3f9a17;
  --ink:#1b1b1b;
  --body:#3a3a3a;
  --pale:#eaf2fd;
  --white:#ffffff;
  --black:#050505;
}
*{box-sizing:border-box;margin:0;padding:0}
html,body{width:1200px;height:3275px;overflow:hidden}
body{font-family:'Poppins',sans-serif;color:var(--ink);background:var(--white);position:relative}
.abs{position:absolute}
.btn{position:absolute;display:flex;align-items:center;justify-content:center;gap:12px;color:var(--white);font-size:15px;border-radius:3px;letter-spacing:.3px}
.btn-navy{background:var(--navy)}
.btn-green{background:var(--green)}
.arrow{width:11px;height:11px}

/* hero */
.hero{left:0;top:0;width:1200px;height:612px;background:linear-gradient(90deg,#eeeeee 0%,#f4f4f4 45%,#e6e2dc 100%)}
.hero-photo{left:642px;top:100px;width:558px;height:512px;background:linear-gradient(135deg,#c9a77a 0%,#d8d2c8 40%,#34508f 80%,#22315a 100%)}
.logo{left:142px;top:43px;font-size:20px;font-weight:600;color:var(--ink)}
.nav{left:534px;top:46px;display:flex;gap:30px;font-size:13.5px;color:var(--ink)}
.nav-quote{left:932px;top:34px;width:127px;height:42px}
.hero-title{left:142px;top:198px;font-size:52px;font-weight:600;line-height:60px;color:#2b2b2b;letter-spacing:.5px}
.hero-sub{left:142px;top:322px;font-size:16px;line-height:27px;color:#2b2b2b}
.hero-btn{left:141px;top:393px;width:127px;height:41px}

/* features */
.features{left:141px;top:559px;width:918px;height:211px;background:linear-gradient(120deg,#1c3390,#24409c 50%,#1a2f86);border-radius:8px;display:flex;justify-content:space-around;padding:40px 70px 0}
.feature{width:180px;text-align:center;color:var(--white);font-size:18px;line-height:21px}
.feature-icon{width:84px;height:84px;border-radius:50%;background:var(--white);margin:0 auto 12px;display:flex;align-items:center;justify-content:center}

/* about */
.about-photo{left:141px;top:855px;width:425px;height:414px;background:linear-gradient(135deg,#9a9a9a,#d6d3cd 50%,#a9a6a0);border-radius:24px}
.about-badge{left:419px;top:1196px;width:177px;height:119px;background:var(--green);border-radius:10px;border:6px solid var(--white);color:var(--white);text-align:center;padding-top:12px}
.about-badge b{display:block;font-size:40px;line-height:44px;font-weight:600}
.about-badge span{font-size:17px;line-height:22px}
.tag{left:643px;top:864px;background:#e3efd9;color:#3b6b22;font-size:13px;padding:3px 11px;border-radius:3px;letter-spacing:1px}
.about-title{left:643px;top:897px;font-size:28px;font-weight:600}
.about-text{left:643px;top:950px;width:415px;font-size:14.5px;line-height:21.3px;color:var(--body)}
.about-text p{margin-bottom:7px}
.about-btn{left:643px;top:1261px;width:135px;height:41px}

/* insurance types */
.types{left:0;top:1404px;width:1200px;height:570px;background:var(--pale)}
.section-title{position:absolute;width:1200px;text-align:center;font-size:27px;font-weight:600;color:var(--ink)}
.card{position:absolute;top:1549px;width:212px;height:244px;border-radius:6px;background:var(--navy-dark);color:var(--white);text-align:center;padding-top:26px}
.card.alt{background:var(--green)}
.card-icon{width:92px;height:92px;border-radius:50%;background:var(--white);border:7px solid rgba(255,255,255,.3);background-clip:padding-box;margin:0 auto 14px;display:flex;align-items:center;justify-content:center}
.card h3{font-size:15px;font-weight:600;margin-bottom:4px}
.card p{font-size:10.8px;line-height:17px;padding:0 4px;white-space:nowrap}
.card-go{position:absolute;left:88px;bottom:-16px;width:35px;height:33px;border-radius:3px;display:flex;align-items:center;justify-content:center;background:var(--green)}
.card.alt .card-go{background:var(--navy-dark)}
.types-btn{left:501px;top:1845px;width:198px;height:42px}

/* partners */
.partner{position:absolute;width:160px;height:118px;background:var(--white);box-shadow:0 2px 10px rgba(0,0,0,.08);display:flex;align-items:center;justify-content:center;text-align:center;font-size:16px;font-weight:600;color:var(--navy-dark);letter-spacing:1px;white-space:nowrap}
.partner.long{font-size:14px;letter-spacing:.5px}

/* quote */
.quote{left:141px;top:2467px;width:918px;height:319px;background:linear-gradient(120deg,#1c3390,#24409c 50%,#1a2f86);border-radius:8px;color:var(--white);text-align:center}
.quote h2{margin-top:76px;font-size:28px;font-weight:600}
.quote p{width:540px;margin:12px auto 0;font-size:15px;line-height:21px}
.quote-btn{left:381px;top:197px;width:155px;height:41px}

/* footer */
.footer{left:0;top:2871px;width:1200px;height:364px;background:var(--black);color:var(--white)}
.f-logo{left:142px;top:91px;font-size:20px;font-weight:600}
.f-about{left:142px;top:145px;width:315px;font-size:13px;line-height:21px;color:var(--white)}
.f-about u{display:block}
.f-col{top:93px}
.f-col h4{font-size:16px;font-weight:500;margin-bottom:22px;position:relative}
.f-col h4::after{content:"";position:absolute;left:0;bottom:-9px;width:32px;height:2px;background:var(--white)}
.f-list li{list-style:none;font-size:13px;line-height:28px;display:flex;align-items:center;gap:8px}
.social li{line-height:41px}
.dot{width:28px;height:28px;border:1px solid var(--white);border-radius:50%}
.contact div{display:flex;gap:12px;font-size:13.5px;line-height:19px;margin-bottom:14px}
.copyright{left:0;top:3235px;width:1200px;height:40px;background:var(--navy);color:var(--white);font-size:12px;text-align:center;line-height:40px}
</style>
</head>
<body>

<section class="abs hero"></section>
<div class="abs hero-photo" role="img" aria-label="Photo of two smiling agents reviewing a tablet together in an office"></div>
<div class="abs logo">BRELLOW COVER INSURANCE</div>
<nav class="abs nav"><span>Home</span><span>About Us</span><span>Insurance Types &#8964;</span><span>Contact Us</span></nav>
<div class="btn btn-navy nav-quote">Get a Quote</div>
<h1 class="abs hero-title">PROTECT WHAT<br>MATTERS MOST</h1>
<p class="abs hero-sub">Comprehensive insurance solutions for your<br>home, vehicle, health, and loved ones</p>
<div class="btn btn-navy hero-btn">Get a Quote</div>

<div class="abs features">
  <div class="feature"><div class="feature-icon"><svg width="40" height="40" viewBox="0 0 40 40" fill="none" stroke="#1a2f86" stroke-width="1.6"><rect x="8" y="5" width="20" height="27" rx="2"/><path d="M12 12h12M12 17h12M12 22h7"/><circle cx="28" cy="28" r="6"/><path d="M25.5 28l2 2 3-3.5"/></svg></div>Insurance<br>Policies</div>
  <div class="feature"><div class="feature-icon"><svg width="44" height="44" viewBox="0 0 44 44" fill="none" stroke="#1a2f86" stroke-width="2"><circle cx="22" cy="22" r="18"/><path d="M15 18q2-3 4 0M25 18q2-3 4 0M13 25q9 10 18 0"/></svg></div>1000+ Happy<br>Clients</div>
  <div class="feature"><div class="feature-icon"><svg width="42" height="42" viewBox="0 0 42 42" fill="none" stroke="#1a2f86" stroke-width="1.7"><circle cx="21" cy="16" r="7"/><path d="M11 17a10 10 0 0120 0M9 36c2-8 22-8 24 0"/><rect x="8" y="15" width="4" height="6" rx="1"/><rect x="30" y="15" width="4" height="6" rx="1"/></svg></div>Professional<br>Support</div>
  <div class="feature"><div class="feature-icon"><svg width="42" height="42" viewBox="0 0 42 42" fill="none" stroke="#1a2f86" stroke-width="1.7"><circle cx="21" cy="21" r="6"/><circle cx="21" cy="21" r="12"/><path d="M21 5v4M21 33v4M5 21h4M33 21h4M10 10l3 3M29 29l3 3M10 32l3-3M29 13l3-3"/></svg></div>Free Lifetime<br>Updates</div>
</div>

<div class="abs about-photo" role="img" aria-label="Photo of an advisor meeting with a senior couple at a table with a laptop"></div>
<div class="abs about-badge"><b>50+</b><span>Skilled<br>Professionals</span></div>
<div class="abs tag">About Us</div>
<h2 class="abs about-title">BRELLOW COVER INSURANCE</h2>
<div class="abs about-text">
  <p>Brellow Cover Insurance is a full-service, independent insurance agency with over three decades of experience in delivering comprehensive insurance solutions to individuals.</p>
  <p>We proudly offer a diverse portfolio of products from more than 20 of the most reputable and financially secure companies in the industry. Our dedicated team of over 50 skilled professionals is committed to customizing these products and services to meet the unique needs of each client.</p>
  <p>At Brellow Cover Insurance, our experts are focused on addressing the individual needs of our clients, ensuring exceptional service and support at every step.</p>
</div>
<div class="btn btn-navy about-btn">Read More <svg class="arrow" viewBox="0 0 10 10" fill="none" stroke="#fff" stroke-width="1.3"><path d="M2 8l6-6M3 2h5v5"/></svg></div>

<section class="abs types"></section>
<h2 class="section-title" style="top:1482px">INSURANCE TYPES</h2>
<div class="card" style="left:141px"><div class="card-icon"><svg width="46" height="46" viewBox="0 0 46 46" fill="none" stroke="#12236b" stroke-width="1.7"><path d="M6 22L23 8l17 14M11 18v20h24V18"/><circle cx="21" cy="27" r="6"/><path d="M21 24v6"/></svg></div><h3>HOMEOWNERS</h3><p>Lorem Ipsum is simply dummy<br>text of the printing typesetting<br>industry Lorem Ipsum has</p><div class="card-go"><svg class="arrow" viewBox="0 0 10 10" fill="none" stroke="#fff" stroke-width="1.3"><path d="M2 8l6-6M3 2h5v5"/></svg></div></div>
<div class="card alt" style="left:376px"><div class="card-icon"><svg width="46" height="46" viewBox="0 0 46 46" fill="none" stroke="#12236b" stroke-width="1.7"><path d="M5 28l4-10h18l4 10v7H5z"/><circle cx="11" cy="30" r="2"/><circle cx="25" cy="30" r="2"/><path d="M35 12l7 3v6c0 5-3 8-7 10-4-2-7-5-7-10v-6z"/></svg></div><h3>AUTO</h3><p>Lorem Ipsum is simply dummy<br>text of the printing typesetting<br>industry Lorem Ipsum has</p><div class="card-go"><svg class="arrow" viewBox="0 0 10 10" fill="none" stroke="#fff" stroke-width="1.3"><path d="M2 8l6-6M3 2h5v5"/></svg></div></div>
<div class="card" style="left:612px"><div class="card-icon"><svg width="46" height="46" viewBox="0 0 46 46" fill="none" stroke="#12236b" stroke-width="1.7"><path d="M11 20L23 10l12 10v12H11z"/><circle cx="23" cy="22" r="3"/><path d="M23 25v5M6 26c0 8 6 14 12 14M40 26c0 8-6 14-12 14"/></svg></div><h3>RENTERS</h3><p>Lorem Ipsum is simply dummy<br>text of the printing typesetting<br>industry Lorem Ipsum has</p><div class="card-go"><svg class="arrow" viewBox="0 0 10 10" fill="none" stroke="#fff" stroke-width="1.3"><path d="M2 8l6-6M3 2h5v5"/></svg></div></div>
<div class="card" style="left:847px"><div class="card-icon"><svg width="46" height="46" viewBox="0 0 46 46" fill="none" stroke="#12236b" stroke-width="1.7"><circle cx="22" cy="8" r="3"/><path d="M22 12v12h10l4 10M22 18h8"/><circle cx="19" cy="30" r="9"/></svg></div><h3>DISABILITY</h3><p>Lorem Ipsum is simply dummy<br>text of the printing typesetting<br>industry Lorem Ipsum has</p><div class="card-go"><svg class="arrow" viewBox="0 0 10 10" fill="none" stroke="#fff" stroke-width="1.3"><path d="M2 8l6-6M3 2h5v5"/></svg></div></div>
<div class="btn btn-navy types-btn">View All Insurance <svg class="arrow" viewBox="0 0 10 10" fill="none" stroke="#fff" stroke-width="1.3"><path d="M2 8l6-6M3 2h5v5"/></svg></div>

<h2 class="section-title" style="top:2052px">OUR PARTNERS</h2>
<div class="partner" style="left:244px;top:2116px">VARNIX</div>
<div class="partner" style="left:427px;top:2116px">OSTLE</div>
<div class="partner long" style="left:611px;top:2116px">MERIDALE MUTUAL</div>
<div class="partner long" style="left:794px;top:2116px">DUNMARROW</div>
<div class="partner" style="left:335px;top:2260px">QUILLOR</div>
<div class="partner" style="left:519px;top:2260px">KGZ</div>
<div class="partner" style="left:703px;top:2260px">PELLWICK</div>

<section class="abs quote">
  <h2>GET A QUOTE TODAY</h2>
  <p>Lorem ipsum dolor sit amet, consectetuer adipiscing elit, sed diam nonummy nibh euismod tincidunt ut laoreet dolore magna aliquam erat volutpat. Ut wisi enim ad minim veniam.</p>
  <div class="btn btn-green quote-btn">Get a Quote <svg class="arrow" viewBox="0 0 10 10" fill="none" stroke="#fff" stroke-width="1.3"><path d="M2 8l6-6M3 2h5v5"/></svg></div>
</section>

<footer class="abs footer">
  <div class="abs f-logo">BRELLOW COVER INSURANCE</div>
  <p class="abs f-about">Lorem ipsum dolor sit amet, consectetuer adipiscing elit, sed diam nonummy nibh euismod tincidunt utted is laoreet dolore magna aliquam erat volutpat. Ut wisi enim ad minim veniam. <u>Read More</u></p>
  <div class="abs f-col" style="left:512px"><h4>Quick Links</h4>
    <ul class="f-list"><li>&raquo; Home</li><li>&raquo; About Us</li><li>&raquo; Insurance Types</li><li>&raquo; Contact Us</li><li>&raquo; Get a Quote</li></ul></div>
  <div class="abs f-col" style="left:690px"><h4>Follow Us</h4>
    <ul class="f-list social"><li><span class="dot"></span>Linkpost</li><li><span class="dot"></span>Streamly</li><li><span class="dot"></span>Snapfold</li><li><span class="dot"></span>Chirpline</li></ul></div>
  <div class="abs f-col contact" style="left:829px"><h4>Contact Details</h4>
    <div><svg width="12" height="16" viewBox="0 0 12 16" fill="#fff"><path d="M6 0a6 6 0 00-6 6c0 4 6 10 6 10s6-6 6-10a6 6 0 00-6-6zm0 8a2 2 0 110-4 2 2 0 010 4z"/></svg><span>Address<br>123 Building Name,<br>City Name, State XY-123456.</span></div>
    <div><svg width="13" height="13" viewBox="0 0 13 13" fill="#fff"><path d="M3 0l2 3-1.5 1.5a8 8 0 005 5L10 8l3 2-1 3C6 13 0 7 0 1z"/></svg><span>Phone<br>(555) 318-2740</span></div>
    <div><svg width="14" height="11" viewBox="0 0 14 11" fill="none" stroke="#fff" stroke-width="1.4"><rect x="1" y="1" width="12" height="9"/><path d="M1 1l6 5 6-5"/></svg><span>Email<br>info@BrellowCover.com</span></div>
  </div>
</footer>
<div class="abs copyright">Copyright © 2025 Brellow Cover Insurance. All Rights Reserved.</div>

</body>
</html>
```